Bramblewood Card Company Business Cards

We are a trading card store with Glimmorax, sports and other TCG cards, we need a business card design that encompasses a clean cut, modern style with a retro flare. website is bramblewoodcardco.com for reference. Can utilize a comic book era feel or a more modern outdoor feel to utilize the "Pacific Northwest" elements of tress, mountains, etc.

Industry/Entity Type

Trading cards and collectibles

Contact Information for Business Card

business name, email address, phone number, name, owner job title

Font styles to use
Sans Serif

```html
<!DOCTYPE html>
<html lang="en">
<head>
<meta charset="utf-8">
<title>Bramblewood Card Company – Business Cards</title>
<link rel="stylesheet" href="https://fonts.googleapis.com/css2?family=Arimo:wght@400;700&display=swap">
<style>
  :root {
    --sky: #0dbde0;
    --slate: #6f6f6f;
    --paper: #ffffff;
    --backdrop: #2b2c2e;
    --ink-light: #ffffff;
  }
  * { margin: 0; padding: 0; box-sizing: border-box; }
  html, body {
    width: 1200px; height: 874px; overflow: hidden;
    background: var(--backdrop);
    font-family: "Arimo", Arial, sans-serif;
  }
  .sheet {
    width: 1200px; height: 874px;
    display: flex; flex-direction: column; align-items: center; justify-content: center;
    gap: 40px;
  }
  .card {
    position: relative;
    width: 620px; height: 354px;
    border-radius: 22px;
    overflow: hidden;
  }
  /* Front */
  .card-front {
    background: var(--sky);
    display: flex; align-items: center; justify-content: center;
  }
  .wordmark {
    display: flex; align-items: center; gap: 14px;
    font-weight: 700; letter-spacing: 1px; text-transform: uppercase;
  }
  .wordmark-mark { width: 18px; height: 18px; border-radius: 50%; }
  .card-front .wordmark { color: var(--paper); font-size: 26px; }
  .card-front .wordmark-mark { background: var(--paper); }

  /* Back */
  .card-back { background: var(--slate); }
  .back-shape { position: absolute; inset: 0; }
  .holder {
    position: absolute; left: 34px; top: 34px;
  }
  .holder-name { color: var(--sky); font-weight: 700; font-size: 27px; line-height: 1; }
  .holder-title { color: var(--ink-light); font-size: 15px; margin-top: 4px; }
  .contacts {
    position: absolute; left: 34px; bottom: 40px;
    list-style: none; color: var(--ink-light); font-size: 16px;
  }
  .contacts li { display: flex; align-items: center; gap: 10px; line-height: 24px; }
  .contacts svg { width: 14px; height: 14px; flex: none; }
  .card-back .wordmark {
    position: absolute; left: 345px; top: 0; width: 250px; height: 354px;
    justify-content: center; text-align: center;
    color: var(--slate); font-size: 20px; line-height: 1.2;
  }
  .card-back .wordmark-mark { background: var(--sky); width: 14px; height: 14px; flex: none; }
</style>
</head>
<body>
<main class="sheet">
  <section class="card card-front" aria-label="Card front">
    <div class="wordmark">
      <span class="wordmark-mark"></span>
      <span>Bramblewood Card Company</span>
    </div>
  </section>

  <section class="card card-back" aria-label="Card back">
    <svg class="back-shape" viewBox="0 0 620 354" width="620" height="354">
      <path d="M412 0 L312 104 Q296 122 296 146 L296 294 Q296 322 312 354 L620 354 L620 0 Z" fill="var(--sky)"/>
      <path d="M424 0 L322 108 Q306 126 306 150 L306 292 Q306 320 322 354 L620 354 L620 0 Z" fill="var(--paper)"/>
    </svg>

    <div class="holder">
      <p class="holder-name">Alder Quinn</p>
      <p class="holder-title">President</p>
    </div>

    <ul class="contacts">
      <li>
        <svg viewBox="0 0 24 24"><path fill="var(--sky)" d="M6.6 10.8a15 15 0 0 0 6.6 6.6l2.2-2.2a1 1 0 0 1 1-.25 11.4 11.4 0 0 0 3.6.57 1 1 0 0 1 1 1V20a1 1 0 0 1-1 1A17 17 0 0 1 3 4a1 1 0 0 1 1-1h3.5a1 1 0 0 1 1 1c0 1.25.2 2.45.57 3.6a1 1 0 0 1-.25 1z"/></svg>
        555-014-7720
      </li>
      <li>
        <svg viewBox="0 0 24 24"><path fill="var(--sky)" d="M2 5h20v14H2z"/><path d="M2 5l10 8 10-8" fill="none" stroke="var(--slate)" stroke-width="2"/></svg>
        info@bramblewoodcardco.com
      </li>
      <li>
        <svg viewBox="0 0 24 24"><circle cx="12" cy="12" r="10" fill="var(--sky)"/><path d="M2 12h20M12 2c3 3 3 17 0 20M12 2c-3 3-3 17 0 20" fill="none" stroke="var(--slate)" stroke-width="1.5"/></svg>
        www.bramblewoodcardco.com
      </li>
    </ul>

    <div class="wordmark">
      <span class="wordmark-mark"></span>
      <span>Bramblewood<br>Card Company</span>
    </div>
  </section>
</main>
</body>
</html>
```